Medical centre needs a business card

We are a medcial centre in Australia, needing a new business card. Our demographic is low working class families. We are going to be renovating our premises to modernise the look and also had a new logo done a few months ago representing quality and community, and now need to update our cards. It needs to be doubled sided, with logo and contact details on the front, and appointment details on the back. . Needs to be modern and simple, easy to read. <br/><br/>Name: Kindle Grove Medical Centre <br/>Address: 512 Parmley Rd (Cnr Parmley Rd & Osgood Creek Rd),<br/>Tindarra Court Shopping Centre, Paralowie, SA 5108<br/>Ph: 08 8461 3072<br/>Tag line: Where your wellbeing comes first<br/>Website: www.kindlegrovemedicalcentre-example.com.au<br/>Online bookings also available<br/><br/>(On the back, to have 3 lines of appointments that can be written in.<br/>Day, date, time)<br/><br/>Your next appointment is on<br/>Can try “M T W Th F Sa Su _________________ at ____________ am/pm” or other combinations <br/>Please advise as soon as possible if unable to attend<br/>Cancellation fees apply if less than 2 hrs notice<br/>Online appointments available (please highlight this option by either by position, colour or font)

Target Market(s)

Lower social economic working class, young families to seniors

Industry/Entity Type

Medical Centre

Contact Information for Business Card

Kindle Grove Medical Centre
512 Parmley Rd (Cnr Parmley Rd & Osgood Creek Drive)
Tindarra Court Shopping Centre
Brenwick SA 5199
Ph: 08 8461 3072
www.kindlegrovemedicalcentre-example.com.au
Tagline line: where your wellbeing comes first
Back side is for appointments
Your next appointment is with Dr ______________
Day/date/time (Please give 3 lines of appointments)
Please advise as soon as possible if unable to attend
Cancellation fees apply if less than 2 hours notice
Online appointments available
Book online easily and conveniently (please highlight online appointments)

Font styles to use
Serif
Sans Serif

Colors

Designer to choose colors to be used in the design.

Requirements
Must have
• Modern and simple
• Easy to ready
• Induces a wellbeing feeling
• Incorporate our logo colours and feel from logo
• Induces feeling of stability and security
Nice to have
• Attract attention
• Pleasant to look at
• Feeling of innovation
Should not have
• Loud clashing colours
• Overly luxurious feeling
• Overly artistic

```html
<!DOCTYPE html>
<html lang="en">
<head>
<meta charset="utf-8">
<title>Kindle Grove Medical Centre – Business Card</title>
<link rel="stylesheet" href="https://fonts.googleapis.com/css2?family=Montserrat:wght@400;500;600;700&family=Roboto+Condensed:wght@400;500&display=swap">
<style>
  :root {
    --bg: #a9a9a9;
    --card: #ffffff;
    --blue: #1473c2;
    --blue-deep: #0b66b8;
    --blue-light: #28a2e0;
    --green: #8cc63f;
    --grey-text: #9a9a9a;
    --line: #b9c3cc;
  }
  * { box-sizing: border-box; margin: 0; padding: 0; }
  html, body { width: 1200px; height: 930px; overflow: hidden; }
  body {
    background: radial-gradient(ellipse at 50% 40%, #c4c4c4 0%, var(--bg) 75%);
    font-family: "Montserrat", sans-serif;
    position: relative;
  }
  .card {
    position: absolute;
    width: 540px;
    height: 330px;
    border-radius: 22px;
    background: var(--card);
    overflow: hidden;
    box-shadow: 0 10px 24px rgba(0,0,0,0.22);
  }

  /* Appointment side */
  .card--appointment { left: 50px; top: 110px; }
  .appt__brand {
    position: absolute; left: 34px; top: 30px;
    font-weight: 700; font-size: 19px; letter-spacing: 0.5px;
    color: var(--blue); text-transform: uppercase;
  }
  .appt__with {
    position: absolute; left: 34px; top: 72px; width: 470px; height: 34px;
    border: 1px solid var(--line);
    font-weight: 500; font-size: 14px; color: var(--blue);
    padding: 8px 10px;
  }
  .appt__row {
    position: absolute; left: 34px;
    font-weight: 600; font-size: 15px; color: var(--blue);
    display: flex; align-items: flex-end; gap: 8px;
  }
  .appt__row--name { top: 122px; width: 470px; }
  .appt__row--date { top: 160px; width: 470px; }
  .fill-line { flex: 1; border-bottom: 1px solid var(--line); height: 16px; }
  .fill-line--short { flex: 0 0 42px; }
  .slash { color: var(--blue); font-weight: 400; }
  .ampm { font-weight: 600; }
  .appt__days {
    position: absolute; left: 34px; top: 200px; width: 470px;
    display: flex; justify-content: space-between;
    font-size: 12.5px; font-weight: 500; color: var(--grey-text);
  }
  .day { display: flex; align-items: center; gap: 5px; }
  .day::before {
    content: ""; width: 9px; height: 9px; border: 1.5px solid var(--green);
  }
  .appt__note {
    position: absolute; left: 34px; top: 228px; width: 480px;
    font-size: 13.5px; line-height: 20px; color: var(--grey-text);
  }
  .appt__band {
    position: absolute; left: 0; bottom: 0; width: 100%; height: 48px;
    background: linear-gradient(90deg, var(--blue-light), var(--blue-deep));
    color: #fff; font-weight: 700; font-size: 15px; letter-spacing: 5px;
    display: flex; align-items: center; justify-content: center;
    text-transform: uppercase;
  }

  /* Contact side */
  .card--contact { left: 610px; top: 480px; }
  .contact__shape { position: absolute; inset: 0; }
  .contact__brand {
    position: absolute; right: 30px; top: 62px; width: 300px; text-align: right;
  }
  .contact__mark {
    display: inline-block; width: 26px; height: 26px; border-radius: 50%;
    background: var(--green); margin-bottom: 10px;
  }
  .contact__name {
    font-weight: 700; font-size: 22px; line-height: 26px; color: var(--blue);
    text-transform: uppercase;
  }
  .contact__tagline {
    margin-top: 8px; font-weight: 500; font-size: 11px; letter-spacing: 1px;
    color: #7a7a7a; text-transform: uppercase;
  }
  .contact__details {
    position: absolute; left: 28px; bottom: 26px;
    font-family: "Roboto Condensed", sans-serif; color: #fff;
    font-size: 14px; line-height: 20px;
  }
  .contact__details .gap { margin-top: 8px; }
</style>
</head>
<body>

  <section class="card card--appointment" aria-label="Appointment side">
    <div class="appt__brand">Kindle Grove Medical Centre</div>
    <div class="appt__with">Your next appointment is with</div>
    <div class="appt__row appt__row--name">Dr. Name :<span class="fill-line"></span></div>
    <div class="appt__row appt__row--date">
      Date :<span class="fill-line fill-line--short"></span><span class="slash">/</span><span class="fill-line fill-line--short"></span><span class="slash">/</span><span class="fill-line fill-line--short"></span>
      &nbsp;Time :<span class="fill-line"></span><span class="ampm">AM/PM</span>
    </div>
    <div class="appt__days">
      <span class="day">MON</span><span class="day">TUE</span><span class="day">WED</span><span class="day">THU</span><span class="day">FRI</span><span class="day">SAT</span><span class="day">SUN</span>
    </div>
    <p class="appt__note">Please advise as soon as possible if unable to attend<br>Cancellation fees apply if less than 2 hours notice.</p>
    <div class="appt__band">Online Appointments Available</div>
  </section>

  <section class="card card--contact" aria-label="Contact side">
    <svg class="contact__shape" viewBox="0 0 540 330" width="540" height="330">
      <defs>
        <linearGradient id="contactBlue" x1="0" y1="0" x2="1" y2="1">
          <stop offset="0" stop-color="#0f7ccb"/>
          <stop offset="0.6" stop-color="#1473c2"/>
          <stop offset="1" stop-color="#2aa3e2"/>
        </linearGradient>
      </defs>
      <path d="M0 0 H128 Q190 245 540 262 V330 H0 Z" fill="url(#contactBlue)"/>
      <path d="M128 0 Q190 245 540 262" fill="none" stroke="#ffffff" stroke-width="8"/>
      <path d="M140 0 Q202 236 540 256" fill="none" stroke="var(--green)" stroke-width="5"/>
    </svg>
    <div class="contact__brand">
      <span class="contact__mark"></span>
      <div class="contact__name">Kindle Grove<br>Medical Centre</div>
      <div class="contact__tagline">Where your wellbeing comes first</div>
    </div>
    <div class="contact__details">
      <div>08 8461 3072</div>
      <div>www.kindlegrovemedicalcentre-example.com.au</div>
      <div class="gap">512 Parmley Rd (Cnr Parmley Rd &amp; Osgood Creek Drive)</div>
      <div>Tindarra Court Shopping Centre</div>
      <div>Brenwick SA 5199</div>
    </div>
  </section>

</body>
</html>
```